Business card for builder specialising in renovations.

Need a card for our building business. Business name is under Martin Powles.
Have licence number on card ( 527691K)
Contact number (0400 382 415)
Want to work on logo for some business cards and shirts - something with MP or MPB or open to ideas??
No animations, No hammers. Something sharp and eye catching.
Highlight that we are a renovation specialist. Simple on front with extra details on back with some lines to jot down things.

Target Market(s)

Renovators

Industry/Entity Type

Building

Contact Information for Business Card

2 sided with room on back to jot things down.
Extra details on back so front can be simple ..like, renovations, bathrooms, decks, extensions, new builds,

Logo Text

MP

Font styles to use
Serif

Requirements
Must have
• Eye catching design .
• Name : Martin powles
• Licence number
• Contact number - 0400382415
Nice to have
• Some logo design that we can carry through to other forms of advertising
• Local builder
• Quality work
Should not have
• No animations

```html
<!DOCTYPE html>
<html lang="en">
<head>
<meta charset="utf-8">
<title>Martin Powles – Business Cards</title>
<link rel="stylesheet" href="https://fonts.googleapis.com/css2?family=Libre+Baskerville&family=PT+Sans:wght@400;700&display=swap">
<style>
  :root {
    --orange: #ec6608;
    --white: #ffffff;
    --paper: #f4f4f4;
    --charcoal: #4a4a4a;
    --backdrop: #e9e6e2;
    --serif: "Libre Baskerville", Georgia, serif;
    --sans: "PT Sans", Arial, sans-serif;
  }
  * { box-sizing: border-box; margin: 0; padding: 0; }
  html, body {
    width: 1200px; height: 900px; overflow: hidden;
    background: var(--backdrop);
  }
  .canvas {
    position: relative; width: 1200px; height: 900px;
    display: flex; flex-direction: column; align-items: center; justify-content: center;
    gap: 40px;
  }
  .card {
    position: relative; width: 640px; height: 366px; overflow: hidden;
    box-shadow: 0 6px 18px rgba(0,0,0,0.18);
  }

  /* Services side */
  .card--services { background: var(--orange); }
  .services__name {
    position: absolute; top: 92px; left: 0; right: 0; text-align: center;
    font-family: var(--serif); font-size: 46px; color: var(--white);
  }
  .services__band {
    position: absolute; top: 190px; left: 0; right: 0; height: 52px;
    background: var(--white);
    display: flex; align-items: center; justify-content: center;
    font-family: var(--sans); font-weight: 700; font-size: 18px; color: var(--orange);
  }
  .services__address {
    position: absolute; top: 270px; left: 0; right: 0; text-align: center;
    font-family: var(--sans); font-size: 15px; color: var(--white); letter-spacing: 0.3px;
  }

  /* Brand side */
  .card--brand { background: linear-gradient(180deg, var(--white) 0%, var(--paper) 100%); }
  .brand__mark {
    position: absolute; top: 34px; left: 0; right: 0;
    display: flex; flex-direction: column; align-items: center; gap: 14px;
  }
  .brand__circle { width: 70px; height: 70px; }
  .brand__wordmark {
    font-family: var(--serif); font-size: 38px; color: var(--charcoal);
  }
  .brand__rule {
    position: absolute; top: 196px; left: 0; right: 0; height: 5px;
    background: var(--charcoal);
  }
  .brand__band {
    position: absolute; top: 208px; left: 0; right: 0; bottom: 0;
    background: var(--orange);
    display: flex; align-items: center; justify-content: center; gap: 30px;
    color: var(--white); font-family: var(--sans);
  }
  .brand__person { font-weight: 700; font-size: 28px; }
  .brand__details { display: flex; flex-direction: column; gap: 6px; font-size: 17px; }
  .brand__licence { font-weight: 700; }
</style>
</head>
<body>
<main class="canvas">
  <section class="card card--services" aria-label="Card back">
    <h1 class="services__name">Martin Powles</h1>
    <p class="services__band">Rrenovations, bathrooms, decks, extensions, new builds etc</p>
    <p class="services__address">12345, Address Goes Here Country Name, 123456.</p>
  </section>

  <section class="card card--brand" aria-label="Card front">
    <div class="brand__mark">
      <svg class="brand__circle" viewBox="0 0 70 70" aria-hidden="true">
        <circle cx="35" cy="35" r="32" fill="none" stroke="#4a4a4a" stroke-width="4"/>
      </svg>
      <span class="brand__wordmark">Martin Powles</span>
    </div>
    <div class="brand__rule"></div>
    <div class="brand__band">
      <span class="brand__person">Martin Powles</span>
      <div class="brand__details">
        <span class="brand__phone">0400 382 415</span>
        <span class="brand__licence">License No- 527691K</span>
      </div>
    </div>
  </section>
</main>
</body>
</html>
```